Wedding Videography Wordpress Website Theme

We need a modern and high-end website look for our wedding video and film business. We film weddings all over the United Kingdom and at European destinations so need something to reflect our work. The website should be visually stunning with images and videos being the focal point as this is what our services are.

The current website is www.brunolessway.com so you will be able to see our brand.

My Instagram is www.instagram.com/brunolesswayfilms so a new design should link in with this idea.

We need the following pages designed by the winning designer

1 - Homepage
2 - Films Index Page
3 - Testimonials
4 - Prices
5 - Reviews
6 - Meet Bruno (About)
7 - Contact
8 - Blog Index
9 - Blog Page

All pages must be consistent so have a similar style.

Pages on menu:
Meet Bruno
Videos
Packages
Testimionials
Journal (Blog)
Contact

We require a responsive look too. Over 90% of our visitors access the website via their mobile devices.

```html
<!DOCTYPE html>
<html lang="en">
<head>
<meta charset="utf-8">
<title>Cara and Leo – Bruno Lessway Wedding Films</title>
<link href="https://fonts.googleapis.com/css2?family=Cormorant+Garamond:wght@500;600&family=Jost:wght@400;500&display=swap" rel="stylesheet">
<style>
:root{
  --gold:#ac9150;
  --gold-soft:#e2d3a8;
  --band:#e8dcb9;
  --ink:#2b2a27;
  --muted:#6f6c66;
  --line:#e3e0d9;
  --white:#fff;
}
*{box-sizing:border-box;margin:0;padding:0}
html,body{width:1200px;height:4717px;overflow:hidden}
body{position:relative;background:var(--white);font-family:'Jost',sans-serif;color:var(--ink)}
.abs{position:absolute}
.serif{font-family:'Cormorant Garamond',serif}
.heading{font-family:'Cormorant Garamond',serif;color:var(--gold);text-transform:uppercase;font-weight:600;text-align:center;left:0;width:1200px;font-size:44px;letter-spacing:1px}
.btn{background:var(--gold-soft);display:flex;align-items:center;justify-content:center;font-size:12px;font-weight:500;letter-spacing:.5px;text-transform:uppercase;color:var(--ink)}

/* hero */
.hero{left:0;top:0;width:1200px;height:616px;background:linear-gradient(160deg,#6b6656 0%,#4a4538 45%,#2f2b24 100%)}
.hero-shade{left:0;top:0;width:1200px;height:616px;background:linear-gradient(180deg,rgba(0,0,0,.35),rgba(0,0,0,.15) 40%,rgba(0,0,0,.4))}
.brand{left:119px;top:74px;width:186px;color:var(--white);font-family:'Cormorant Garamond',serif;font-weight:600;font-size:20px;letter-spacing:4px;text-align:center;line-height:1}
.brand small{display:block;font-family:'Jost',sans-serif;font-size:8px;letter-spacing:5px;margin-top:6px;font-weight:400}
.nav a{position:absolute;top:80px;color:var(--white);font-size:11px;text-transform:uppercase;text-decoration:none;letter-spacing:.4px}
.nav .active:after{content:"";position:absolute;left:5px;right:5px;bottom:-10px;height:2px;background:var(--white)}
.hero-title{left:0;width:1200px;top:296px;text-align:center;color:var(--white);font-size:38px;font-weight:500;text-transform:uppercase;letter-spacing:1px}
.hero-sub{left:0;width:1200px;top:352px;text-align:center;color:var(--white);font-size:16px}
.hero-date{left:0;width:1200px;top:398px;display:flex;justify-content:center;align-items:center;gap:14px;color:var(--white);font-size:16px}

/* intro */
.photo{background:linear-gradient(135deg,#2d3550,#6b5a48 60%,#b7a58c)}
.arrow-btn{display:flex;align-items:center;justify-content:center;width:52px;height:40px}
.intro-title{left:733px;top:752px;font-size:38px;color:var(--gold);font-weight:500}
.intro-sub{left:733px;top:810px;font-size:19px;font-weight:500}
.body-text{font-size:12.5px;line-height:26px;color:var(--muted)}

/* suppliers */
.band{left:0;width:1200px;background:var(--band)}
.supplier{background:var(--white);height:106px;width:310px;display:flex;align-items:center;padding-left:32px;gap:26px}
.supplier .icon{width:56px;height:56px;background:#efe6cc;border-radius:4px}
.supplier small{display:block;font-size:11px;color:var(--muted);margin-bottom:6px}
.supplier b{font-weight:500;font-size:18px}

/* post nav */
.social{display:flex;gap:14px}
.social span{width:24px;height:24px;border:1.5px solid var(--gold);border-radius:5px;display:block}

/* related */
.post-img{width:475px;height:362px}
.badge{width:73px;height:77px;background:var(--gold);color:var(--white);text-align:center;padding-top:8px}
.badge b{display:block;font-family:'Cormorant Garamond',serif;font-size:36px;line-height:1;font-weight:600}
.badge small{font-size:9px;text-transform:uppercase;letter-spacing:1px}
.post-title{font-family:'Cormorant Garamond',serif;font-size:20px;font-weight:600}
.excerpt{font-size:10.5px;color:var(--muted)}
.read-more{font-size:12px;color:var(--gold);display:flex;align-items:center;gap:10px}
.read-more:after{content:"";width:28px;height:1px;background:var(--gold)}

/* instagram */
.insta-title{left:0;width:1200px;top:4016px;text-align:center;font-family:'Cormorant Garamond',serif;font-size:28px;letter-spacing:7px;color:var(--ink);text-transform:uppercase}
.insta{top:4096px;width:145px;height:162px}

/* footer */
.foot-h{font-size:16px;font-weight:500;display:flex;align-items:center;gap:12px}
.foot-h:after{content:"";width:26px;height:1px;background:var(--muted)}
.foot-l{font-size:12px;color:var(--muted)}
</style>
</head>
<body>

<!-- hero -->
<header>
  <div class="abs hero" role="img" aria-label="Bride and groom laughing under falling confetti"></div>
  <div class="abs hero-shade"></div>
  <div class="abs brand">BRUNO LESSWAY<small>WEDDING FILMS</small></div>
  <nav class="nav">
    <a style="left:397px">Meet Bruno</a>
    <a style="left:511px">Videos</a>
    <a style="left:597px">Packages</a>
    <a style="left:709px">Testimonials</a>
    <a class="active" style="left:837px">Journal</a>
  </nav>
  <div class="abs btn" style="left:940px;top:64px;width:145px;height:44px">Enquire</div>
  <h1 class="abs hero-title serif">Cara and Leo</h1>
  <p class="abs hero-sub">Harrow Fell Inn Old Barn Wedding</p>
  <p class="abs hero-date">
    <svg width="26" height="26" viewBox="0 0 26 26" fill="none" stroke="#fff" stroke-width="1.5"><rect x="2" y="4" width="22" height="20" rx="3"/><path d="M2 10h22M8 1v6M18 1v6"/></svg>
    12 August 2022 - Weddings
  </p>
</header>

<!-- intro -->
<section>
  <div class="abs photo" style="left:115px;top:683px;width:557px;height:385px" role="img" aria-label="Groom waiting as the bride walks down the barn aisle"></div>
  <div class="abs arrow-btn" style="left:568px;top:1028px;background:#fff">
    <svg width="22" height="12" viewBox="0 0 22 12" fill="none" stroke="#888" stroke-width="1.4"><path d="M21 6H1M6 1L1 6l5 5"/></svg>
  </div>
  <div class="abs arrow-btn" style="left:620px;top:1028px;background:var(--gold-soft)">
    <svg width="22" height="12" viewBox="0 0 22 12" fill="none" stroke="#2b2a27" stroke-width="1.4"><path d="M1 6h20M16 1l5 5-5 5"/></svg>
  </div>
  <h2 class="abs intro-title serif">Leo and Cara's</h2>
  <p class="abs intro-sub serif">Harrow Fell Inn Old Barn Wedding</p>
  <p class="abs body-text" style="left:733px;top:852px;width:330px">Phasellus enim libero, blandit vel sapien vitae, condimentum ultricies magna et. Quisque euismod orci ut. Phasellus enim libero, blandit vel sapien vitae, condimentum ultricies magna et. Quisque euismod orci ut.</p>
</section>

<!-- highlights -->
<section>
  <p class="abs" style="left:0;width:1200px;top:1157px;text-align:center;font-size:15px;color:var(--muted)">Highlights</p>
  <h2 class="abs heading" style="top:1190px">Harrow Fell Inn</h2>
  <div class="abs" style="left:115px;top:1266px;width:970px;height:396px;background:linear-gradient(180deg,#9a8f95 0%,#b8a9a4 22%,#5d6b4c 40%,#3f4a33 75%,#4e5838 100%)" role="img" aria-label="Aerial view of the inn and surrounding countryside"></div>
  <svg class="abs" style="left:580px;top:1444px" width="40" height="40" viewBox="0 0 40 40"><circle cx="20" cy="20" r="19" fill="rgba(255,255,255,.75)"/><path d="M16 13l11 7-11 7z" fill="#555"/></svg>
  <div class="abs arrow-btn" style="left:96px;top:1458px;width:46px;height:40px;background:#fff">
    <svg width="22" height="12" viewBox="0 0 22 12" fill="none" stroke="#888" stroke-width="1.4"><path d="M21 6H1M6 1L1 6l5 5"/></svg>
  </div>
  <div class="abs arrow-btn" style="left:1055px;top:1458px;width:53px;height:40px;background:var(--gold-soft)">
    <svg width="22" height="12" viewBox="0 0 22 12" fill="none" stroke="#2b2a27" stroke-width="1.4"><path d="M1 6h20M16 1l5 5-5 5"/></svg>
  </div>
  <div class="abs" style="left:293px;top:1689px;width:137px;height:97px;background:linear-gradient(135deg,#3f6a3a,#8aa36a)" role="img" aria-label="Inn entrance with garden"></div>
  <div class="abs" style="left:452px;top:1689px;width:138px;height:97px;background:linear-gradient(135deg,#b9ad99,#e4dccd)" role="img" aria-label="Bridesmaids in pale dresses"></div>
  <div class="abs" style="left:610px;top:1689px;width:137px;height:97px;background:linear-gradient(135deg,#3a2620,#7a4d3a)" role="img" aria-label="Cake stand with desserts"></div>
  <div class="abs" style="left:769px;top:1689px;width:138px;height:97px;background:linear-gradient(135deg,#8fa2b4,#d9dfe3)" role="img" aria-label="Decorated reception room"></div>
  <p class="abs body-text" style="left:270px;top:1820px;width:660px;text-align:center;line-height:26px;font-size:12px">Phasellus enim libero, blandit vel sapien vitae, condimentum ultricies magna et. Quisque euismod orci ut. Phasellus enim libero, blandit vel sapien vitae, condimentum ultricies magna et. Quisque euismod orci ut. Phasellus enim libero, blandit vel sapien vitae, condimentum ultricies magna et.</p>
</section>

<!-- suppliers -->
<section>
  <div class="abs band" style="top:1962px;height:520px"></div>
  <h2 class="abs heading" style="top:2020px">Suppliers</h2>
  <div class="abs supplier" style="left:114px;top:2129px"><div class="icon" role="img" aria-label="Venue icon"></div><div><small>Venue:</small><b>Harrow Fell Inn</b></div></div>
  <div class="abs supplier" style="left:445px;top:2129px"><div class="icon" role="img" aria-label="Photographer icon"></div><div><small>Photographer:</small><b>RL Studio</b></div></div>
  <div class="abs supplier" style="left:775px;top:2129px"><div class="icon" role="img" aria-label="Hair stylist icon"></div><div><small>Hair:</small><b>Ivy Marsh</b></div></div>
  <div class="abs supplier" style="left:278px;top:2279px"><div class="icon" role="img" aria-label="Make up icon"></div><div><small>Make Up:</small><b>Nell Porter</b></div></div>
  <div class="abs supplier" style="left:608px;top:2279px"><div class="icon" role="img" aria-label="Florist icon"></div><div><small>Florist:</small><b>Petal Loft</b></div></div>
</section>

<!-- post navigation -->
<section>
  <p class="abs" style="left:114px;top:2533px;font-size:11px;color:var(--muted)">Previous Post</p>
  <p class="abs serif" style="left:114px;top:2556px;font-size:21px;font-weight:600">Ashby Hall Wedding In Northumberland</p>
  <div class="abs social" style="left:799px;top:2549px"><span></span><span></span><span style="width:32px"></span></div>
  <div class="abs btn" style="left:964px;top:2537px;width:121px;height:44px;text-transform:none;gap:12px;font-size:12px">
    <svg width="20" height="20" viewBox="0 0 20 20" fill="none" stroke="#2b2a27" stroke-width="1.3"><circle cx="15" cy="4" r="2.5"/><circle cx="4" cy="10" r="2.5"/><circle cx="15" cy="16" r="2.5"/><path d="M6.3 8.8l6.4-3.6M6.3 11.2l6.4 3.6"/></svg>
    10 Shares
  </div>
  <div class="abs" style="left:114px;top:2627px;width:971px;height:1px;background:var(--line)"></div>
</section>

<!-- related posts -->
<section>
  <h2 class="abs heading" style="top:2680px">Related Posts</h2>

  <article>
    <div class="abs post-img" style="left:114px;top:2785px;background:linear-gradient(135deg,#4c4a46,#8b837a)" role="img" aria-label="Couple embracing in a garden"></div>
    <div class="abs badge" style="left:125px;top:2796px"><b>12</b><small>Aug</small></div>
    <h3 class="abs post-title" style="left:114px;top:3168px">Ashby Hall Wedding In Northumberland</h3>
    <p class="abs excerpt" style="left:114px;top:3212px">Gorgeous wedding at the stunning and quirky Ashby Hall in Northumberland.</p>
    <p class="abs read-more" style="left:116px;top:3248px">Read More</p>
  </article>
  <article>
    <div class="abs post-img" style="left:608px;top:2785px;background:linear-gradient(135deg,#7fa7c8,#c9d9e4 50%,#6c5a4c)" role="img" aria-label="Guests throwing blue confetti over the couple"></div>
    <div class="abs badge" style="left:619px;top:2796px"><b>08</b><small>Aug</small></div>
    <h3 class="abs post-title" style="left:608px;top:3168px">The Romantic Wedding at the Red Lion Elmsford</h3>
    <p class="abs excerpt" style="left:608px;top:3212px">The Romantic Wedding at the Red Lion Elmsford</p>
    <p class="abs read-more" style="left:610px;top:3248px">Read More</p>
  </article>
  <article>
    <div class="abs post-img" style="left:114px;top:3296px;background:linear-gradient(135deg,#6b4a1f,#a47a3a 50%,#5a3d18)" role="img" aria-label="Aerial shot of couple lying in a golden field"></div>
    <div class="abs badge" style="left:125px;top:3307px"><b>12</b><small>Aug</small></div>
    <h3 class="abs post-title" style="left:114px;top:3679px">Ashby Hall Wedding In Northumberland</h3>
    <p class="abs excerpt" style="left:114px;top:3723px">Gorgeous wedding at the stunning and quirky Ashby Hall in Northumberland.</p>
    <p class="abs read-more" style="left:116px;top:3759px">Read More</p>
  </article>
  <article>
    <div class="abs post-img" style="left:608px;top:3296px;background:linear-gradient(135deg,#3a2f28,#8a7564 55%,#c9b79e)" role="img" aria-label="Couple laughing during church ceremony"></div>
    <div class="abs badge" style="left:619px;top:3307px"><b>08</b><small>Aug</small></div>
    <h3 class="abs post-title" style="left:608px;top:3679px">The Romantic Wedding at the Red Lion Elmsford</h3>
    <p class="abs excerpt" style="left:608px;top:3723px">The Romantic Wedding at the Red Lion Elmsford</p>
    <p class="abs read-more" style="left:610px;top:3759px">Read More</p>
  </article>

  <div class="abs btn" style="left:493px;top:3853px;width:212px;height:45px">Load More Testimonials</div>
</section>

<!-- instagram -->
<section>
  <div class="abs band" style="top:3952px;height:467px"></div>
  <h2 class="abs insta-title">Follow Me On Instagram</h2>
  <div class="abs insta" style="left:114px;background:linear-gradient(160deg,#cfc9c1,#6b6560)" role="img" aria-label="Couple walking down a street"></div>
  <div class="abs insta" style="left:279px;background:linear-gradient(160deg,#bfc3c6,#4a4b52)" role="img" aria-label="Groom with bride in a courtyard"></div>
  <div class="abs insta" style="left:444px;background:linear-gradient(180deg,#e4e6e1,#7d8a5a)" role="img" aria-label="Horse drawn carriage in a field"></div>
  <div class="abs insta" style="left:609px;background:linear-gradient(160deg,#e8e6e2,#2a2a2c)" role="img" aria-label="Groom and groomsman in suits"></div>
  <div class="abs insta" style="left:774px;background:linear-gradient(160deg,#4a4f4a,#1f2220)" role="img" aria-label="Groom portrait"></div>
  <div class="abs insta" style="left:939px;background:linear-gradient(180deg,#c8d4de,#7c8a6a)" role="img" aria-label="Wedding party jumping outdoors"></div>
  <div class="abs" style="left:471px;top:4309px;width:256px;height:55px;background:#fff;display:flex;align-items:center;justify-content:center;font-size:13px">Follow me @brunolesswayfilms</div>
</section>

<!-- footer -->
<footer>
  <div class="abs serif" style="left:104px;top:4535px;width:206px;text-align:center;color:var(--gold);font-weight:600;font-size:18px;letter-spacing:3px">BRUNO LESSWAY<span style="display:block;font-family:'Jost',sans-serif;font-size:7px;letter-spacing:4px;font-weight:400">WEDDING FILMS</span></div>
  <div class="abs social" style="left:153px;top:4603px"><span></span><span></span><span style="width:32px"></span></div>

  <p class="abs foot-h" style="left:412px;top:4496px">Contact</p>
  <svg class="abs" style="left:412px;top:4545px" width="18" height="18" viewBox="0 0 18 18" fill="none" stroke="#8a8781" stroke-width="1.2"><path d="M4 1.5l3 3.5-2 2c1 2.2 3 4.2 5 5l2-2 3.5 3-2 2.5C8 16 2 10 1.5 4z"/></svg>
  <p class="abs foot-l" style="left:450px;top:4546px">07000 318 264</p>
  <svg class="abs" style="left:412px;top:4596px" width="18" height="14" viewBox="0 0 18 14" fill="none" stroke="#8a8781" stroke-width="1.2"><rect x="1" y="1" width="16" height="12"/><path d="M1 1l8 7 8-7"/></svg>
  <p class="abs foot-l" style="left:450px;top:4594px">films@brunolessway.com</p>

  <p class="abs foot-h" style="left:700px;top:4497px">Links</p>
  <p class="abs foot-l" style="left:703px;top:4541px">FAQ's</p>
  <p class="abs foot-l" style="left:703px;top:4574px">Wedding Photography</p>
  <p class="abs foot-l" style="left:703px;top:4607px">Commercial</p>
  <p class="abs foot-l" style="left:918px;top:4541px">North East Wedding Venues</p>
  <p class="abs foot-l" style="left:918px;top:4574px">Free Speeches Guide</p>
  <p class="abs foot-l" style="left:918px;top:4607px">Blog</p>

  <p class="abs" style="left:0;width:1200px;top:4674px;text-align:center;font-size:10px;color:#9a978f">© Copyright 2022 Bruno Lessway Films Ltd All Rights Reserved</p>
</footer>

</body>
</html>
```